Website Development for vaultmerrow.com.au

Build a new Wordpress/Responsive website for vaultmerrow.com.au

Target Market(s)

Compliance Managers, Risk Managers, Information Security and Cyber Security Professionals, Chief Data/Digital Officers, Chief Operating/Financial Officers, Business Continuity Professionals, Disaster Recovery Planners, Small Business Owners, Local/Federal Government entities

Industry/Entity Type

Data Service

Coding

Coded - Design and coding required

Number of Pages Required

5+ page

Font styles to use
Sans Serif

Colors

Designer to choose colors to be used in the design.

Requirements
Must have
• 1. Site Structure: Home Page plus the following chapter-pages for a) Services b) About c) Resources d) Blog e) Contact Us
• 2. Prefer site to built on wordpress and we can purchase a theme if needed (we currently use Kelp9 for other sites)
• 3. Blog needs to be wordpress based
• 4. We will host the site ourselves on our own servers
• 5. Responsive Design
Nice to have
• 1. Livechat capability/interface
• 2. Capability for marketing automation integration (such as hubspot, marketo, infusionsoft etc)
• 3. Capability for CRM integration (Salesforce)

```html
<!DOCTYPE html>
<html lang="en">
<head>
<meta charset="utf-8">
<title>Vault Merrow — Data Service</title>
<link rel="stylesheet" href="https://fonts.googleapis.com/css2?family=Lato:wght@400;700;900&family=Open+Sans:wght@400;600&display=swap">
<style>
:root{
  --red:#e41e2b;
  --red-dark:#c0131f;
  --ink:#222;
  --text:#666;
  --muted:#999;
  --light:#f3f3f3;
  --footer:#1d1d1d;
  --white:#fff;
}
*{box-sizing:border-box;margin:0;padding:0}
html,body{width:1200px;height:4204px;overflow:hidden}
body{position:relative;background:var(--white);font-family:"Open Sans",Arial,sans-serif;color:var(--text)}
.abs{position:absolute}
h1,h2,h3,h4,.nav a,.btn,.logo{font-family:"Lato",Arial,sans-serif}

/* header */
.site-header{left:0;top:0;width:1200px;height:135px;background:var(--white)}
.logo{left:112px;top:40px;display:flex;align-items:center;gap:12px;font-weight:900;font-size:30px;color:var(--red);letter-spacing:1px}
.logo-dot{width:40px;height:40px;border-radius:50%;background:var(--red)}
.nav{right:110px;top:58px;display:flex;gap:24px}
.nav a{font-size:15px;font-weight:700;color:#333;text-decoration:none;text-transform:uppercase}
.nav a.active{color:var(--red)}

/* hero */
.hero{left:0;top:135px;width:1200px;height:700px}
.hero-title{left:110px;top:340px;font-size:48px;font-weight:900;color:var(--white);letter-spacing:1px}
.hero-sub{left:110px;top:405px;font-size:20px;font-weight:600;color:var(--white);line-height:1.35}
.btn{display:inline-flex;align-items:center;gap:8px;height:40px;padding:0 24px;border-radius:20px;font-size:14px;font-weight:700;color:var(--white);text-transform:uppercase}
.btn-red{background:var(--red)}
.btn-ghost{border:2px solid rgba(255,255,255,.6)}
.hero-btns{left:110px;top:503px;display:flex;gap:18px}
.arrow{top:395px;width:30px;height:46px;background:var(--red);display:flex;align-items:center;justify-content:center}

/* section heads */
.watermark{width:1200px;left:0;text-align:center;font-family:"Lato",sans-serif;font-weight:900;font-size:92px;color:#f1f1f1;text-transform:uppercase}
.sec-title{width:1200px;left:0;text-align:center;font-size:40px;font-weight:900;color:var(--ink);text-transform:uppercase}
.sec-line{left:570px;width:60px;height:3px;background:var(--red)}
.sec-text{left:330px;width:540px;text-align:center;font-size:14px;line-height:1.6;color:var(--muted)}

/* services */
.service{width:300px;text-align:center}
.service svg{display:block;margin:0 auto 10px}
.service h3{font-size:19px;font-weight:900;color:var(--red-dark);text-transform:uppercase;margin-bottom:8px}
.service p{font-size:14px;line-height:1.5;color:var(--muted)}
.hub{left:535px;top:1355px;width:130px;height:130px;border-radius:50%;background:var(--red)}
.dot{width:10px;height:10px;border-radius:50%;background:var(--red)}

/* about */
.about-watermark{left:4px;top:1830px;writing-mode:vertical-rl;transform:rotate(180deg);font-family:"Lato",sans-serif;font-weight:900;font-size:86px;line-height:1;color:#e4e4e4;white-space:nowrap}
.about-title{left:110px;top:1905px;font-size:40px;font-weight:900;color:var(--ink);text-transform:uppercase}
.about-line{left:110px;top:1962px;width:60px;height:3px;background:var(--red)}
.about-text{left:110px;width:500px;font-size:15px;line-height:1.65;color:var(--text)}
.about-img{left:640px;top:1925px;width:445px;height:320px}
.play{left:598px;top:2168px;width:64px;height:64px;border-radius:50%;background:var(--white);border:4px solid var(--red);display:flex;align-items:center;justify-content:center}

/* resources */
.res-card{width:290px;background:var(--white);box-shadow:0 4px 14px rgba(0,0,0,.2)}
.res-card .ph{height:180px}
.res-card h4{height:60px;line-height:60px;text-align:center;font-size:20px;font-weight:900;color:var(--ink);text-transform:uppercase}

/* blog */
.post-main{left:110px;top:3250px;width:485px;height:370px;background:var(--white);box-shadow:0 3px 12px rgba(0,0,0,.12)}
.post-main .ph{height:200px}
.date{left:22px;top:0;width:56px;height:78px;background:var(--red);color:var(--white);text-align:center;font-family:"Lato",sans-serif;font-weight:700;padding-top:10px;font-size:13px}
.date b{display:block;font-size:26px;font-weight:900;line-height:1.1}
.post-main h4{padding:30px 24px 12px;font-size:24px;font-weight:700;color:var(--ink)}
.post-main p{padding:0 24px;font-size:14px;line-height:1.6;color:var(--muted)}
.post-side{left:630px;width:455px;height:130px;background:var(--white);box-shadow:0 3px 12px rgba(0,0,0,.12);display:flex}
.post-side .ph{width:80px;height:100%;flex:none}
.post-side .txt{padding:14px 16px}
.post-side h4{font-size:16px;font-weight:700;color:var(--ink);line-height:1.3;margin-bottom:8px}
.meta{font-size:12px;color:var(--red);margin-bottom:6px;display:flex;align-items:center;gap:6px}
.post-side p{font-size:13px;line-height:1.5;color:var(--muted)}

/* footer */
.footer{left:0;top:3712px;width:1200px;height:492px;background:var(--footer)}
.f-col{top:3850px}
.f-col h4{font-size:17px;font-weight:900;color:var(--white);text-transform:uppercase;margin-bottom:6px}
.f-col .bar{width:40px;height:2px;background:var(--red);margin-bottom:18px}
.f-col li{list-style:none;font-size:14px;color:#bbb;margin-bottom:12px;display:flex;align-items:center;gap:10px}
.f-col li::before{content:"";width:6px;height:6px;border-top:2px solid var(--red);border-right:2px solid var(--red);transform:rotate(45deg)}
.f-col.contact li::before,.f-col.social li::before{display:none}
.f-col.contact li{align-items:flex-start}
.ic{width:14px;height:14px;border-radius:50%;background:#888;flex:none}
.copy{left:0;top:4110px;width:1200px;text-align:center;font-size:13px;color:#aaa}
.f-line{left:0;top:4085px;width:1200px;height:1px;background:#333}

.livechat{right:0;top:1580px;width:40px;height:140px;background:var(--red);border-radius:6px 0 0 6px;color:var(--white);font-family:"Lato",sans-serif;font-weight:700;font-size:15px;writing-mode:vertical-rl;transform:rotate(180deg);display:flex;align-items:center;justify-content:center}
</style>
</head>
<body>

<header class="site-header abs">
  <div class="logo abs"><span class="logo-dot"></span>VAULT MERROW</div>
  <nav class="nav abs">
    <a class="active">Home</a><a>Services</a><a>About</a><a>Resources</a><a>Blog</a><a>Contact Us</a>
  </nav>
</header>

<section class="hero abs">
  <svg width="1200" height="700" style="position:absolute;left:0;top:0">
    <defs>
      <linearGradient id="heroFill" x1="0" y1="0" x2="1" y2="1">
        <stop offset="0" stop-color="#0d1a2e"/><stop offset=".55" stop-color="#1d3a63"/><stop offset="1" stop-color="#0a1424"/>
      </linearGradient>
    </defs>
    <polygon points="0,640 600,700 1200,640 1200,620 600,678 0,620" fill="#e41e2b"/>
    <polygon points="0,0 1200,0 1200,625 600,682 0,625" fill="url(#heroFill)" role="img" aria-label="Server room with lines of code on a screen"/>
  </svg>
</section>
<h1 class="hero-title abs">CYBER SECURITY</h1>
<p class="hero-sub abs">Lorem ipsum dolor sit amet, consectetur adipiscing<br>elit sed do eiusmod tempor.</p>
<div class="hero-btns abs">
  <span class="btn btn-red">Read More ›</span>
  <span class="btn btn-ghost">Whitepaper ›</span>
</div>
<div class="arrow abs" style="left:0"><svg width="10" height="16"><path d="M8 2 2 8l6 6" stroke="#fff" stroke-width="2" fill="none"/></svg></div>
<div class="arrow abs" style="right:0"><svg width="10" height="16"><path d="M2 2l6 6-6 6" stroke="#fff" stroke-width="2" fill="none"/></svg></div>

<!-- services -->
<div class="watermark abs" style="top:905px">Our Services</div>
<h2 class="sec-title abs" style="top:950px">Our Services</h2>
<div class="sec-line abs" style="top:1005px"></div>
<p class="sec-text abs" style="top:1020px">Lorem ipsum dolor sit amet, consectetur adipiscing elit sed do eiusmod tempor incididunt ut labore et dolore magna aliqua. Ut enim ad minim veniam, quis nostrud exercitation ullamco.</p>

<div class="service abs" style="left:240px;top:1115px">
  <svg width="40" height="40"><rect x="4" y="4" width="32" height="32" rx="4" fill="none" stroke="#e41e2b" stroke-width="3"/><path d="M12 26l6-8 5 5 6-9" stroke="#e41e2b" stroke-width="3" fill="none"/></svg>
  <h3>Risk Management</h3><p>Lorem ipsum dolor sit amet consectetur<br>adipiscing elit sed do eiusmod</p>
</div>
<div class="service abs" style="left:650px;top:1115px">
  <svg width="40" height="40"><path d="M20 4 34 9v10c0 9-6 14-14 17C12 33 6 28 6 19V9z" fill="none" stroke="#e41e2b" stroke-width="3"/></svg>
  <h3>Cyber Security</h3><p>Lorem ipsum dolor sit amet consectetur<br>adipiscing elit sed do eiusmod</p>
</div>
<div class="service abs" style="left:110px;top:1300px">
  <svg width="40" height="40"><rect x="8" y="18" width="24" height="18" rx="3" fill="none" stroke="#e41e2b" stroke-width="3"/><path d="M13 18v-5a7 7 0 0 1 14 0v5" fill="none" stroke="#e41e2b" stroke-width="3"/></svg>
  <h3>Information Security</h3><p>Lorem ipsum dolor sit amet consectetur<br>adipiscing elit sed do eiusmod</p>
</div>
<div class="service abs" style="left:790px;top:1300px">
  <svg width="40" height="40"><rect x="5" y="6" width="30" height="22" rx="3" fill="none" stroke="#e41e2b" stroke-width="3"/><path d="M14 34h12M20 28v6" stroke="#e41e2b" stroke-width="3"/></svg>
  <h3>Disaster Recovery</h3><p>Lorem ipsum dolor sit amet consectetur<br>adipiscing elit sed do eiusmod</p>
</div>
<div class="service abs" style="left:200px;top:1470px">
  <svg width="40" height="40"><rect x="8" y="4" width="24" height="32" rx="3" fill="none" stroke="#e41e2b" stroke-width="3"/><path d="M13 20l5 5 9-10" stroke="#e41e2b" stroke-width="3" fill="none"/></svg>
  <h3>Compliance Management</h3><p>Lorem ipsum dolor sit amet consectetur<br>adipiscing elit sed do eiusmod</p>
</div>
<div class="service abs" style="left:650px;top:1470px">
  <svg width="40" height="40"><rect x="4" y="8" width="22" height="16" rx="2" fill="none" stroke="#e41e2b" stroke-width="3"/><rect x="16" y="18" width="20" height="16" rx="2" fill="none" stroke="#e41e2b" stroke-width="3"/></svg>
  <h3>Digital Management</h3><p>Lorem ipsum dolor sit amet consectetur<br>adipiscing elit sed do eiusmod</p>
</div>

<div class="hub abs"></div>
<div class="dot abs" style="left:595px;top:1300px"></div>
<div class="dot abs" style="left:595px;top:1532px"></div>
<div class="dot abs" style="left:485px;top:1340px"></div>
<div class="dot abs" style="left:705px;top:1340px"></div>
<div class="dot abs" style="left:485px;top:1495px"></div>
<div class="dot abs" style="left:705px;top:1495px"></div>
<div class="dot abs" style="left:465px;top:1418px"></div>
<div class="dot abs" style="left:725px;top:1418px"></div>

<!-- about -->
<svg class="abs" style="left:0;top:1740px" width="1200" height="610">
  <path d="M0 40 Q300 0 600 30 T1200 20 V610 H0Z" fill="#f3f3f3"/>
</svg>
<div class="about-watermark abs">ABOUT US</div>
<h2 class="about-title abs">About Us</h2>
<div class="about-line abs"></div>
<p class="about-text abs" style="top:1985px">Lorem ipsum dolor sit amet, consectetur adipiscing elit, sed do eiusmod tempor incididunt ut labore et dolore magna aliqua.</p>
<p class="about-text abs" style="top:2060px">Ut enim ad minim veniam, quis nostrud exercitation ullamco laboris nisi ut aliquip ex ea commodo consequat. Duis aute irure dolor in reprehenderit in voluptate velit esse cillum dolore eu fugiat nulla pariatur.</p>
<span class="btn btn-red abs" style="left:110px;top:2195px">Read More ›</span>
<div class="about-img abs" role="img" aria-label="Businessman working at a laptop in an office" style="background:linear-gradient(135deg,#dfe6ee,#a9b7c6 60%,#e9edf1)"></div>
<div class="play abs"><svg width="18" height="20"><path d="M3 2l13 8-13 8z" fill="#e41e2b"/></svg></div>

<div class="livechat abs">Live chat</div>

<!-- resources -->
<svg class="abs" style="left:0;top:2340px" width="1200" height="710">
  <polygon points="0,10 1200,0 1200,630 600,700 0,630" fill="#e41e2b"/>
</svg>
<div class="watermark abs" style="top:2400px;color:rgba(255,255,255,.12)">Our Resources</div>
<h2 class="sec-title abs" style="top:2445px;color:#fff">Our Resources</h2>
<div class="sec-line abs" style="top:2500px;background:#fff"></div>
<div class="res-card abs" style="left:112px;top:2545px">
  <div class="ph" role="img" aria-label="Hands reviewing financial charts on a desk" style="background:linear-gradient(135deg,#4a4f57,#a6acb4)"></div>
  <h4>Financial Overview</h4>
</div>
<div class="res-card abs" style="left:455px;top:2545px">
  <div class="ph" role="img" aria-label="Team discussing work at a computer" style="background:linear-gradient(135deg,#3e444d,#8f9aa6)"></div>
  <h4>Whitepaper</h4>
</div>
<div class="res-card abs" style="left:795px;top:2545px">
  <div class="ph" role="img" aria-label="Colleagues working at desks with monitors" style="background:linear-gradient(135deg,#c9ced4,#6f7984)"></div>
  <h4>Data Management</h4>
</div>

<!-- blog -->
<div class="watermark abs" style="top:3100px">Blog Posts</div>
<h2 class="sec-title abs" style="top:3145px">From The Blog</h2>
<div class="sec-line abs" style="top:3200px"></div>

<article class="post-main abs">
  <div class="ph" role="img" aria-label="Business team meeting around a table" style="background:linear-gradient(135deg,#c3c9d0,#7d8893)"></div>
  <div class="date abs">JAN<b>20</b></div>
  <h4>Lorem ipsum dolor sit, consectetur</h4>
  <p>Ut enim ad minim veniam, quis nostrud exercitation ullamco laboris nisi ut aliquip ex ea commodo consequat duis aute.</p>
</article>
<article class="post-side abs" style="top:3252px">
  <div class="ph" role="img" aria-label="Hands typing on a laptop" style="background:linear-gradient(135deg,#d6dbe0,#98a3ae)"></div>
  <div class="txt">
    <h4>Nemo enim ipsam volutem sdit<br>volupted aspernatur odit</h4>
    <div class="meta"><svg width="10" height="10"><rect x="1" y="1" width="8" height="8" fill="none" stroke="#e41e2b"/></svg>Jan 12, 2019</div>
    <p>Lorem ipsum dolor sit amet, consectetur adipiscing elit.</p>
  </div>
</article>
<article class="post-side abs" style="top:3470px">
  <div class="ph" role="img" aria-label="Person working on code at night" style="background:linear-gradient(135deg,#1f3a3a,#4f6f6c)"></div>
  <div class="txt">
    <h4>Nemo enim ipsam volutem sdit<br>volupted aspernatur odit</h4>
    <div class="meta"><svg width="10" height="10"><rect x="1" y="1" width="8" height="8" fill="none" stroke="#e41e2b"/></svg>Jan 08, 2019</div>
    <p>Lorem ipsum dolor sit amet, consectetur adipiscing elit.</p>
  </div>
</article>

<!-- footer -->
<div class="abs" style="left:0;top:3692px;width:1200px;height:20px;background:#e8e8e8"></div>
<footer class="footer abs"></footer>
<div class="f-col abs" style="left:112px">
  <h4>Quick Links</h4><div class="bar"></div>
  <ul><li>Home</li><li>About Us</li><li>Services</li><li>Blog</li><li>Contact Us</li></ul>
</div>
<div class="f-col abs" style="left:345px">
  <h4>Other Links</h4><div class="bar"></div>
  <ul><li>Help</li><li>Support</li><li>Newsletter</li><li>FAQs</li><li>Terms Of Services</li></ul>
</div>
<div class="f-col contact abs" style="left:595px">
  <h4>Contact Us</h4><div class="bar"></div>
  <ul>
    <li><svg width="14" height="16"><path d="M7 15S1 9 1 6a6 6 0 0 1 12 0c0 3-6 9-6 9z" fill="#e41e2b"/></svg><span>1234, Sample Street, Sample<br>City, New State.</span></li>
    <li><svg width="14" height="14"><path d="M3 1l3 3-2 2a9 9 0 0 0 4 4l2-2 3 3-2 2C6 13 1 8 1 3z" fill="#e41e2b"/></svg>(+1) 123 456 7890</li>
    <li><svg width="14" height="12"><rect x="1" y="1" width="12" height="10" fill="none" stroke="#e41e2b" stroke-width="1.5"/><path d="M1 1l6 5 6-5" stroke="#e41e2b" fill="none" stroke-width="1.5"/></svg>support@vaultmerrow.com.au</li>
  </ul>
</div>
<div class="f-col social abs" style="left:965px">
  <h4>Follow Us</h4><div class="bar"></div>
  <ul><li><span class="ic"></span>Community</li><li><span class="ic"></span>Updates</li><li><span class="ic"></span>Gallery</li><li><span class="ic"></span>Boards</li></ul>
</div>
<div class="f-line abs"></div>
<p class="copy abs">© Copyright 2019 Vault Merrow. All Rights Reserved.</p>

</body>
</html>
```